Podiatry clinic requires a modern revamp and editing of existing website.

I would like a fresh new look and updated information for my current business website. An easy to navigate site with prominent address and phone number for call to action. We are a podiatry clinic that focuses on general and sports podiatry.
I would like 4 pages; including Home page, About Us, Services & Contact.
www.brambleridgepodiatry.net

Target Market(s)

Active working professionals.

Industry/Entity Type

Medical

Coding

Coded - Design and coding required

Number of Pages Required

4 page

Font styles to use
Sans Serif

Colors
6b449b

Requirements
Must have
• A modern look with logo and active images; clean and uncluttered. Visible phone number and address for call to action.
• 4 pages - Home, About Us, Services, Contact.
• Home page - update address & service logos.
• About Us - update of personal information.
• Services - Revamp of existing page.
• Contact page to include Google map, email & phone number.
Nice to have
• Ability to add content easily; eg. a blog or adding video onto Home page.
• Link to Facebook page.

```html
<!DOCTYPE html>
<html lang="en">
<head>
<meta charset="utf-8">
<title>Bramble Ridge Podiatry</title>
<link href="https://fonts.googleapis.com/css2?family=Roboto:wght@400;500;700&family=Open+Sans:wght@400;600&family=Sacramento&family=League+Spartan:wght@700&display=swap" rel="stylesheet">
<style>
:root{
  --purple:#6b449b;
  --purple-light:#8567b5;
  --blue:#1ea4dc;
  --navy:#2d3f6e;
  --ink:#222;
  --muted:#555;
  --pale:#f2f2f6;
  --footer-text:#c9b8e6;
  --white:#fff;
}
*{margin:0;padding:0;box-sizing:border-box}
html,body{width:1200px;height:2375px;overflow:hidden;background:var(--white)}
body{font-family:"Roboto",Arial,sans-serif;color:var(--ink);position:relative}
.abs{position:absolute}

/* top nav */
.topnav{top:0;left:0;width:1200px;height:52px;background:var(--white)}
.topnav ul{list-style:none;display:flex;gap:30px;position:absolute;left:472px;top:17px}
.topnav a{font-size:13px;font-weight:500;color:var(--navy);text-decoration:none;text-transform:uppercase}
.social{position:absolute;top:6px;left:955px;display:flex;gap:8px}
.social span{width:35px;height:35px;border-radius:3px;display:block}
.social .s1{background:#3b5998}.social .s2{background:#29a8e0}.social .s3{background:#1a7ab9}

/* header band */
.header{top:52px;left:0;width:1200px;height:119px;background:var(--purple-light);border-top:3px solid var(--purple)}
.brand{position:absolute;left:127px;top:38px;display:flex;align-items:center;gap:12px}
.brand-mark{width:30px;height:30px;border-radius:50%;background:var(--white)}
.brand-name{font-family:"Roboto",sans-serif;font-weight:700;font-size:24px;color:var(--white)}
.header-contact{position:absolute;left:772px;top:18px;padding-left:12px;border-left:1px solid #b7a3d8;color:var(--white);font-size:14px;line-height:22px}

/* hero */
.hero{top:171px;left:0;width:1200px;height:491px;background:linear-gradient(180deg,#bfbfbf 0%,#8d8d8d 55%,#5d5d5d 100%)}
.hero-title{position:absolute;width:100%;top:62px;text-align:center;font-family:"Sacramento",cursive;font-weight:400;color:var(--white);font-size:70px;line-height:88px}
.hero-sub{position:absolute;width:100%;top:246px;text-align:center;color:var(--white);font-size:19px;line-height:30px}
.hero-btns{position:absolute;top:330px;width:100%;display:flex;justify-content:center;gap:50px}
.btn{font-size:10px;font-weight:700;text-transform:uppercase;height:30px;line-height:30px;border-radius:3px;text-align:center}
.btn-solid{background:var(--white);color:var(--navy);width:72px}
.btn-ghost{border:1px solid var(--white);color:var(--white);width:96px}
.dots{position:absolute;top:458px;left:566px;display:flex;gap:10px}
.dots i{width:9px;height:9px;border-radius:50%;background:var(--white);display:block}
.dots i.off{background:transparent;border:1px solid var(--white)}

/* quote band */
.quote{top:662px;left:0;width:1200px;height:229px;background:var(--purple)}
.quote p{position:absolute;left:137px;top:48px;width:620px;font-family:"League Spartan",sans-serif;font-weight:700;color:var(--white);font-size:32px;line-height:37px;text-transform:uppercase;white-space:nowrap}
.portrait{top:668px;left:792px;width:254px;height:252px;background:var(--white);padding:14px;transform:rotate(3deg);box-shadow:0 4px 10px rgba(0,0,0,.3)}
.portrait div{width:100%;height:100%;background:linear-gradient(160deg,#8a6a55,#c9a38a 60%,#b9a8a0)}

/* about */
.about-photo{top:934px;left:127px;width:302px;height:443px;background:linear-gradient(170deg,#3c4a2c,#8a7a55 50%,#c9b59a)}
.about-text{top:938px;left:450px;width:623px;text-align:center}
.about-kicker{font-size:15px;font-weight:400;color:var(--navy);padding-bottom:8px;border-bottom:2px solid #9fa8c4}
.about-lead{margin-top:22px;font-size:26px;line-height:31px;color:var(--blue)}
.about-body{margin-top:12px;font-family:"Open Sans",sans-serif;font-size:19px;line-height:33px;color:#333}
.about-small{margin-top:14px;font-family:"Open Sans",sans-serif;font-size:13px;line-height:22px;color:#333}

/* products */
.products-title{top:1404px;left:0;width:1200px;text-align:center;font-size:22px;font-weight:500;color:var(--ink)}
.dotted{top:1445px;left:52px;width:1097px;border-top:2px dotted #777}
.card{top:1502px;width:347px;text-align:center}
.card .img{height:231px}
.card h3{margin-top:24px;font-size:19px;font-weight:500;color:var(--ink)}
.card p{margin-top:14px;font-family:"Open Sans",sans-serif;font-size:12.5px;line-height:20px;color:var(--muted);padding:0 8px}
.c1{left:52px}.c2{left:427px}.c3{left:802px}
.c1 .img{background:linear-gradient(120deg,#f2e8e2,#e4c6b4 55%,#f6f1ee)}
.c2 .img{background:linear-gradient(180deg,#f5f5f5,#e3c9a8 55%,#e8e8e8)}
.c3 .img{background:linear-gradient(180deg,#3b8fd6 0%,#9cc9ee 45%,#6a9a3a 70%,#3c6a22 100%)}

/* partners */
.partners{top:1912px;left:0;width:1200px;height:157px;background:var(--pale)}
.badge{position:absolute;background:#9a9a9a}
.b1{left:60px;top:58px;width:230px;height:40px;border-radius:20px;background:#7a7a7a}
.b2{left:365px;top:56px;width:185px;height:44px;border-radius:6px;background:#8c8c8c}
.b3{left:620px;top:30px;width:245px;height:90px;border-radius:8px;background:#6e6e6e}
.b4{left:957px;top:36px;width:187px;height:60px;background:#8a8a8a}

/* footer */
.footer{top:2069px;left:0;width:1200px;height:306px;background:var(--purple);color:var(--footer-text)}
.fcol{position:absolute;top:50px;width:260px}
.fcol h4{font-size:17px;font-weight:500;color:var(--white);margin-bottom:18px}
.fcol p{font-size:12.5px;line-height:20px}
.fcol p + p{margin-top:12px}
.fcol .lbl{color:var(--white)}
.f1{left:52px}.f2{left:332px}.f3{left:614px}.f4{left:896px}
.fb-dot{display:block;width:10px;height:12px;background:var(--footer-text);margin-top:22px;border-radius:2px}
.footer-rule{position:absolute;top:245px;left:52px;width:1097px;border-top:1px solid #7f5daf}
.footer-bottom{position:absolute;top:270px;left:52px;width:1097px;display:flex;justify-content:space-between;font-size:12.5px;color:var(--white)}
</style>
</head>
<body>

<nav class="topnav abs">
  <ul>
    <li><a href="#">Home</a></li>
    <li><a href="#">About Us</a></li>
    <li><a href="#">Services</a></li>
    <li><a href="#">Blog</a></li>
  </ul>
  <div class="social"><span class="s1"></span><span class="s2"></span><span class="s3"></span></div>
</nav>

<header class="header abs">
  <div class="brand"><span class="brand-mark"></span><span class="brand-name">Bramble Ridge Podiatry</span></div>
  <div class="header-contact">
    Suite 27 / 115 Harlow Street Ashford 3100<br>
    1300 555 248<br>
    info@brambleridgepodiatry.net
  </div>
</header>

<section class="hero abs" role="img" aria-label="Black and white photo of a runner's legs and shoes on a misty road">
  <h1 class="hero-title">Welcome to<br>Bramble Ridge Podiatry</h1>
  <p class="hero-sub">We are a podiatry clinic that focuses<br>on general and sports podiatry</p>
  <div class="hero-btns"><span class="btn btn-solid">About Us</span><span class="btn btn-ghost">Go on surfing</span></div>
  <div class="dots"><i></i><i class="off"></i><i></i><i></i></div>
</section>

<section class="quote abs">
  <p>“I take great personal<br>satisfaction in helping my<br>patients return, pain free, to<br>the activities that they love.”</p>
</section>
<div class="portrait abs"><div role="img" aria-label="Portrait photo of the clinic's podiatrist"></div></div>

<div class="about-photo abs" role="img" aria-label="Photo of a runner kneeling and holding his knee on a path"></div>
<section class="about-text abs">
  <h2 class="about-kicker">Welcome to Bramble Ridge Podiatry</h2>
  <p class="about-lead">Bramble Ridge Podiatry is a Podiatry clinic in the heart of Ashford city centre. We are located between Elm &amp; Carter Streets in the Harlow Business Centre.</p>
  <p class="about-body">Our podiatrists are fully qualified health professionals who are able to diagnose, treat, manage or help to prevent all medical conditions that affect the feet and lower limb.</p>
  <p class="about-small">We provide General Podiatry Treatment and some Specialised Services in relation to various foot conditions, including Sports Injuries, Orthotic Therapy and Nail Surgery.</p>
</section>

<h2 class="products-title abs">Podiatry &amp; Footwear Wellness Products</h2>
<div class="dotted abs"></div>

<article class="card c1 abs">
  <div class="img" role="img" aria-label="Photo of hands massaging a foot"></div>
  <h3>Podiatry Treatments</h3>
  <p>Podiatrists are trained to diagnose and treat all medical conditions that affect the feet and lower limb. At Bramble Ridge Podiatry we provide treatment for general &amp; Sports Podiatry conditions and various specialised treatments.</p>
</article>
<article class="card c2 abs">
  <div class="img" role="img" aria-label="Photo of an orthotic insole held under a foot"></div>
  <h3>Podiatry Products Footwear</h3>
  <p>At Bramble Ridge Podiatry we stock and recommend various products and footwear that aid in maintaining optimal foot health</p>
</article>
<article class="card c3 abs">
  <div class="img" role="img" aria-label="Photo of a family walking through a sunny green field"></div>
  <h3>Health Wellness Products</h3>
  <p>At Bramble Ridge Podiatry, we believe that maintaining a healthy &amp; active lifestyle is the best way to prevent or manage debilitating foot conditions. We like to promote a healthy diet &amp; nutrition proper hydration and skin care</p>
</article>

<section class="partners abs">
  <span class="badge b1"></span>
  <span class="badge b2"></span>
  <span class="badge b3"></span>
  <span class="badge b4"></span>
</section>

<footer class="footer abs">
  <div class="fcol f1">
    <h4>Contact</h4>
    <p>Please feel free to contact us for any issue. Our staff is available to you from 9AM until 5PM on weekdays.</p>
    <span class="fb-dot"></span>
  </div>
  <div class="fcol f2">
    <h4>Phone number</h4>
    <p><span class="lbl">Phone 1:</span> 1300 555 248</p>
    <p><span class="lbl">Phone 2:</span> 1300 555 248</p>
  </div>
  <div class="fcol f3">
    <h4>Office</h4>
    <p><span class="lbl">Address:</span> Suite 27 / 115 Harlow Street</p>
    <p><span class="lbl">City:</span> Ashford 3100</p>
  </div>
  <div class="fcol f4">
    <h4>E-Mail</h4>
    <p><span class="lbl">Info:</span> info@brambleridgepodiatry.net</p>
  </div>
  <div class="footer-rule"></div>
  <div class="footer-bottom">
    <span>Copyright © 2016 Sports Podiatry Ashford</span>
    <span>Website: www.brambleridgepodiatry.net</span>
  </div>
</footer>

</body>
</html>
```